Business Card Design for Property Development Company Director

I am looking for a professional and unforgettable business card design for our Director of our Property Development Company.
Please see attached .pptx file to find out what information to include. You don't have to follow the exact format shown in the file - I am interested to see your creative flair using the information provided.

```html
<!DOCTYPE html>
<html lang="en">
<head>
<meta charset="utf-8">
<title>Harwell Property Group – Business Card</title>
<link href="https://fonts.googleapis.com/css2?family=Roboto:wght@400;500;700&family=Roboto+Condensed:wght@700&display=swap" rel="stylesheet">
<style>
  :root {
    --bg: #e4e5e7;
    --card: #f7f7f7;
    --blue: #274a96;
    --blue-dark: #1f3f84;
    --grey: #58595b;
    --grey-light: #7a7b7d;
    --faint: #ebebeb;
  }
  * { box-sizing: border-box; margin: 0; padding: 0; }
  html, body { width: 1200px; height: 726px; overflow: hidden; }
  body {
    background: var(--bg);
    font-family: "Roboto", Arial, sans-serif;
    position: relative;
  }
  .card {
    position: absolute;
    top: 204px;
    width: 520px;
    height: 318px;
    background: var(--card);
    box-shadow: 0 6px 18px rgba(0,0,0,0.12);
    overflow: hidden;
  }
  .card--front { left: 50px; }
  .card--back { left: 630px; }

  /* Front */
  .tagline {
    position: absolute; top: 34px; left: 0; right: 0;
    text-align: center; color: var(--blue);
    font-size: 19px; line-height: 1.2; font-weight: 400;
  }
  .brand {
    display: flex; align-items: center; gap: 12px;
    color: var(--blue); font-weight: 700;
  }
  .brand__mark { background: var(--grey); flex: none; }
  .brand__name { line-height: 1; }
  .brand__name small { display: block; font-weight: 700; letter-spacing: 0.18em; }
  .card--front .brand { position: absolute; top: 108px; left: 92px; }
  .card--front .brand__mark { width: 44px; height: 44px; }
  .card--front .brand__name { font-size: 40px; letter-spacing: 0.02em; }
  .card--front .brand__name small { font-size: 15px; margin-top: 4px; }
  .pitch {
    position: absolute; top: 190px; left: 0; right: 0;
    text-align: center; color: var(--grey); font-size: 14.5px;
  }
  .pitch strong { color: var(--blue); font-weight: 400; }
  .split-bar { position: absolute; top: 218px; left: 0; right: 0; height: 9px; display: flex; }
  .split-bar__grey { flex: 0 0 58%; background: var(--grey-light); }
  .split-bar__blue { flex: 1; background: var(--blue); }

  /* Back */
  .side-band { position: absolute; top: 0; bottom: 0; left: 0; width: 66px; background: var(--blue-dark); }
  .side-rule { position: absolute; top: 0; bottom: 0; left: 72px; width: 3px; background: var(--grey); }
  .watermark { position: absolute; top: 60px; right: -30px; width: 230px; height: 230px; background: var(--faint); }
  .card--back .brand { position: absolute; top: 40px; left: 96px; }
  .card--back .brand__mark { width: 34px; height: 34px; }
  .card--back .brand__name { font-size: 29px; }
  .card--back .brand__name small { font-size: 11px; margin-top: 3px; }
  .person { position: absolute; top: 126px; left: 96px; }
  .person__name { font-family: "Roboto Condensed", "Arial Narrow", sans-serif; font-weight: 700; font-size: 22px; color: var(--blue); }
  .person__role { font-size: 13px; color: var(--grey); margin-top: 4px; }
  .contacts { position: absolute; top: 190px; left: 96px; list-style: none; color: var(--grey); font-size: 15px; }
  .contacts li { display: flex; align-items: center; gap: 12px; height: 22px; }
  .contacts svg { width: 14px; height: 14px; fill: var(--grey); flex: none; }
  .licence { margin-top: 6px; }
  .licence span { color: var(--blue); }
</style>
</head>
<body>

<section class="card card--front" aria-label="Card front">
  <p class="tagline">Property Development<br>&amp; Site Acquisition Specialists</p>
  <div class="brand">
    <span class="brand__mark"></span>
    <span class="brand__name">HARWELL<small>PROPERTY GROUP</small></span>
  </div>
  <p class="pitch">Ask me about our <strong>INVESTMENT &amp; PARTNERSHIP</strong> opportunities</p>
  <div class="split-bar"><span class="split-bar__grey"></span><span class="split-bar__blue"></span></div>
</section>

<section class="card card--back" aria-label="Card back">
  <div class="side-band"></div>
  <div class="side-rule"></div>
  <div class="watermark"></div>
  <div class="brand">
    <span class="brand__mark"></span>
    <span class="brand__name">HARWELL<small>PROPERTY GROUP</small></span>
  </div>
  <div class="person">
    <p class="person__name">Daniel Mercer</p>
    <p class="person__role">Director</p>
  </div>
  <ul class="contacts">
    <li>
      <svg viewBox="0 0 24 24" aria-hidden="true"><path d="M6.6 10.8a15 15 0 0 0 6.6 6.6l2.2-2.2c.3-.3.7-.4 1-.2 1.1.4 2.3.6 3.6.6.6 0 1 .4 1 1V20c0 .6-.4 1-1 1A17 17 0 0 1 3 4c0-.6.4-1 1-1h3.5c.6 0 1 .4 1 1 0 1.3.2 2.5.6 3.6.1.3 0 .7-.2 1z"/></svg>
      0400 123 456
    </li>
    <li>
      <svg viewBox="0 0 24 24" aria-hidden="true"><path d="M2 5h20v14H2z M4 7v.5l8 5 8-5V7l-8 5z" fill-rule="evenodd"/></svg>
      daniel@harwell.com.au
    </li>
    <li>
      <svg viewBox="0 0 24 24" aria-hidden="true"><path d="M12 2a10 10 0 1 0 0 20 10 10 0 0 0 0-20zm0 2c.9 1.2 1.6 2.8 1.9 5h-3.8c.3-2.2 1-3.8 1.9-5zM4.3 11h3.8c0-.7.1-1.4.2-2H5a8 8 0 0 0-.7 2zm0 2a8 8 0 0 0 .7 2h3.3c-.1-.6-.2-1.3-.2-2zm5.8 0c0 .7.1 1.4.2 2h3.4c.1-.6.2-1.3.2-2zm0-2h3.8c0-.7-.1-1.4-.2-2h-3.4c-.1.6-.2 1.3-.2 2zm5.8 0h3.8a8 8 0 0 0-.7-2h-3.3c.1.6.2 1.3.2 2zm0 2c0 .7-.1 1.4-.2 2H19a8 8 0 0 0 .7-2zM12 20c-.9-1.2-1.6-2.8-1.9-5h3.8c-.3 2.2-1 3.8-1.9 5z"/></svg>
      www.harwell.com.au
    </li>
    <li class="licence">Real Estate Lic: <span>&nbsp;1234567 &amp; 1234568</span></li>
  </ul>
</section>

</body>
</html>
```